BRAMBLEFORD CONSTRUCTIONS B-Card

I currently have a b-card design but will be removing the image (tree) from the logo and have text only.
I want the card to be classy and strong within the building and construction industry.
I will be using Spot UV on the cards as per the attached examples. I will also send through some sketched ideas that I have in mind.
The color blue is similar to the image (No. 6) attached images

Target Market(s)

middle to maturre aged.
Home Owners / Renovators and Builders

Industry/Entity Type

Construction

Contact Information for Business Card

BRAMBLEFORD CONSTRUCTIONS
Name: Gareth Pennick
Title: Project Manager
Mobile: 0427 351 804
Office: (08) 9316 5172
Address: 47C Corvell Street, Malaga WA 6090
Email: info@bramblefordhomes.com.au
PO Box: 3817 Tarrowvale WA 6872

Colors
0592cd
33a6d7
85cae6
1b1b1b

Requirements
Must have
• 1. It must have spot UV on the front of card, maybe back of card too
• 2. I really like the blue on image 6. (or at least a really cool electric blue against the charcoal grey background)
• 3. The font must be slimline and modern. Easy to read
• 4. There must be no black used on the card... Only greys and dark charcoal greys
• 5. Use only the text from the logo "Brambleford Constructions" Not the image of the tree. I am wanting the b-cards to be more masculine.
Nice to have
• 1. I like the design concept on image 6. but happy to see what else you can do with the Spot UV
• 2. Unless you have a really cool idea of the image of the tree (from previous logo) Spot UV somewhere in the design concept thats original and different then I am keen to see what you come up with
• 3. Try changing the color of the logo eg. full white or Blue and white
• 4. Another option is to have the Brambleford Logo on the front of card with the spot UV in the background of text which we specialise in eg, Roofing, Ceiling, Insulation, Gutter Guards, Electrical, Insurance etc and we can add or reduce items as required. Similar to image 12.
Should not have
• Do not include the image of the tree from previous logo. unless you have a really cool idea of Spot UV somewhere in the design concept thats original and different.

```html
<!DOCTYPE html>
<html lang="en">
<head>
<meta charset="utf-8">
<title>Brambleford Constructions – Business Card</title>
<link rel="stylesheet" href="https://fonts.googleapis.com/css2?family=Source+Sans+3:wght@300;400;600;700&display=swap">
<style>
  :root {
    --backdrop: #3b3b3b;
    --card: #1d1d1d;
    --card-panel: #222222;
    --blue: #33a6d7;
    --blue-deep: #0592cd;
    --text: #ededed;
    --text-soft: #c9c9c9;
  }
  * { box-sizing: border-box; margin: 0; padding: 0; }
  html, body {
    width: 1200px;
    height: 900px;
    overflow: hidden;
  }
  body {
    background: var(--backdrop);
    font-family: "Source Sans 3", "PT Sans", sans-serif;
    position: relative;
  }
  .card {
    position: absolute;
    top: 310px;
    width: 460px;
    height: 281px;
    background: var(--card);
    border-radius: 16px;
    box-shadow: 0 10px 26px rgba(20, 20, 20, 0.55);
    overflow: hidden;
  }
  .card--contact { left: 80px; }
  .card--brand { left: 660px; }

  /* Contact side */
  .brand-mark {
    position: absolute;
    left: 48px;
    top: 58px;
    width: 166px;
    height: 166px;
    border-radius: 50%;
    background: var(--blue);
    display: flex;
    align-items: center;
    justify-content: center;
  }
  .brand-mark__name {
    color: var(--text);
    font-size: 15px;
    font-weight: 600;
    letter-spacing: 1.5px;
  }
  .contact-panel {
    position: absolute;
    left: 250px;
    top: 0;
    right: 0;
    bottom: 0;
    background: var(--card-panel);
    padding: 52px 0 0 24px;
  }
  .contact__name {
    color: var(--blue);
    font-size: 19px;
    font-weight: 600;
    line-height: 1.1;
  }
  .contact__title {
    color: var(--text-soft);
    font-size: 12px;
    margin-top: 3px;
  }
  .contact__address {
    color: var(--text);
    font-size: 13px;
    line-height: 1.45;
    margin-top: 22px;
    font-style: normal;
  }
  .contact__phones {
    list-style: none;
    margin-top: 18px;
  }
  .contact__phone {
    color: var(--text);
    font-size: 13px;
    line-height: 1.55;
    display: flex;
    align-items: center;
    gap: 6px;
  }
  .contact__icon {
    width: 10px;
    height: 12px;
    fill: var(--blue);
  }

  /* Brand side */
  .wordmark {
    position: absolute;
    inset: 0;
    display: flex;
    flex-direction: column;
    align-items: center;
    justify-content: center;
    color: var(--blue);
    text-align: center;
  }
  .wordmark__primary {
    font-size: 40px;
    font-weight: 700;
    letter-spacing: 0.5px;
    line-height: 1;
  }
  .wordmark__secondary {
    font-size: 16px;
    font-weight: 300;
    letter-spacing: 8.5px;
    margin-top: 6px;
    padding-left: 8px;
  }
</style>
</head>
<body>
  <section class="card card--contact" aria-label="Business card, contact side">
    <div class="brand-mark">
      <span class="brand-mark__name">BRAMBLEFORD</span>
    </div>
    <div class="contact-panel">
      <h1 class="contact__name">Gareth Pennick</h1>
      <p class="contact__title">Project Manager</p>
      <address class="contact__address">
        47C Corvell Street, Tarrowvale<br>
        WA 6871 PO Box: 3817<br>
        Tarrowvale WA 6872
      </address>
      <ul class="contact__phones">
        <li class="contact__phone">
          <svg class="contact__icon" viewBox="0 0 10 12" aria-hidden="true">
            <path d="M2 0.5 L3.6 0.3 L4.4 3 L3.2 4 C3.6 5.6 4.6 7 5.8 8 L7 7.2 L9.4 8.6 L9 10.4 C8.6 11.4 7.4 11.8 6 11 C3.2 9.4 1 6.6 0.6 3.4 C0.4 2 1 0.8 2 0.5 Z"/>
          </svg>
          0427 351 804
        </li>
        <li class="contact__phone">
          <svg class="contact__icon" viewBox="0 0 10 12" aria-hidden="true">
            <path d="M2 0 H8 A1.2 1.2 0 0 1 9.2 1.2 V10.8 A1.2 1.2 0 0 1 8 12 H2 A1.2 1.2 0 0 1 0.8 10.8 V1.2 A1.2 1.2 0 0 1 2 0 Z M2 1.4 V9.4 H8 V1.4 Z"/>
          </svg>
          (08) 9316 5172
        </li>
      </ul>
    </div>
  </section>

  <section class="card card--brand" aria-label="Business card, brand side">
    <div class="wordmark">
      <span class="wordmark__primary">BRAMBLEFORD</span>
      <span class="wordmark__secondary">CONSTRUCTIONS</span>
    </div>
  </section>
</body>
</html>
```